Business card for law firm

Need business card for new law firm. Think confident, authoritative, conservative, but not stuffy or old-fashioned.

Contact Information for Business Card

Content for card - logo (uploaded), plus the following:

Paul Whitcombe (larger font)
Managing Partner (larger font, but not as large as name)
Level 9, 7 Ferris Lane
Sydney NSW 2000
Main Tel 02 9364 2710
Direct Tel 02 8472 3159
Email paul@qvlegal.com.au
www.qvlegal.com.au

Letterhead design should include logo plus:
Level 9, 7 Ferris Lane
Sydney NSW 2000
Tel 02 8472 3159
www.qvlegal.com.au

```html
<!DOCTYPE html>
<html lang="en">
<head>
<meta charset="utf-8">
<title>Quayvale Lawyers – Letterhead</title>
<link rel="stylesheet" href="https://fonts.googleapis.com/css2?family=Questrial&family=Roboto:wght@400&display=swap">
<style>
  :root {
    --backdrop: #e9e9ea;
    --paper-light: #f7f7f7;
    --paper-dark: #e4e4e5;
    --navy: #0f1f4f;
    --text-grey: #6f6f6f;
    --salutation-grey: #8a8a8a;
    --signature-blue: #d3dcec;
    --white: #ffffff;
  }
  * { box-sizing: border-box; margin: 0; padding: 0; }
  html, body {
    width: 1024px;
    height: 1200px;
    overflow: hidden;
    background: var(--backdrop);
  }
  .letterhead {
    position: absolute;
    left: 102px;
    top: 25px;
    width: 820px;
    height: 1150px;
    background: linear-gradient(160deg, var(--paper-light) 0%, var(--paper-dark) 100%);
    font-family: "Questrial", "Century Gothic", sans-serif;
    color: var(--text-grey);
    overflow: hidden;
  }
  .brand {
    position: absolute;
    top: 68px;
    left: 0;
    width: 100%;
    text-align: center;
    color: var(--navy);
  }
  .brand-mark {
    display: block;
    width: 38px;
    height: 38px;
    margin: 0 auto 14px;
    background: var(--navy);
  }
  .brand-name {
    font-size: 27px;
    letter-spacing: 2px;
    line-height: 1;
  }
  .brand-descriptor {
    font-size: 9px;
    letter-spacing: 7px;
    margin-top: 5px;
    padding-left: 7px;
  }
  .letter {
    position: absolute;
    left: 77px;
    top: 298px;
    width: 676px;
  }
  .salutation {
    font-size: 20px;
    color: var(--salutation-grey);
    margin-bottom: 40px;
  }
  .letter-body p {
    font-size: 11.7px;
    line-height: 15.2px;
    text-align: justify;
    margin-bottom: 18px;
  }
  .closing {
    font-size: 11.7px;
    margin-top: 32px;
  }
  .signature {
    display: block;
    width: 140px;
    height: 66px;
    margin-top: 46px;
    background: linear-gradient(120deg, var(--signature-blue), #e6ebf4);
    border-radius: 4px;
  }
  .footer-band {
    position: absolute;
    left: 0;
    bottom: 0;
    width: 820px;
    height: 130px;
  }
  .footer-contact {
    position: absolute;
    left: 0;
    bottom: 20px;
    width: 100%;
    text-align: center;
    font-family: "Roboto", Arial, sans-serif;
    font-size: 14px;
    color: var(--white);
  }
</style>
</head>
<body>
  <main class="letterhead">
    <header class="brand">
      <span class="brand-mark"></span>
      <div class="brand-name">QUAYVALE</div>
      <div class="brand-descriptor">LAWYERS</div>
    </header>

    <section class="letter">
      <p class="salutation">Dear Mr. Hartley,</p>
      <div class="letter-body">
        <p>Lorem ipsum dolor sit amet, consectetur adipiscing elit. Donec orci purus, luctus vitae dignissim eu, iaculis sed purus. Vivamus faucibus, ipsum nec aliquet viverra, leo mauris condimentum ligula, sit amet sagittis enim ligula quis arcu. Nam egestas tortor id nisi porttitor mattis. In tortor ante, ultricies in suscipit a, tempus non massa. Vivamus et auctor mi. Fusce vel massa nulla. Phasellus nec eros mauris, et scelerisque orci.</p>
        <p>Donec malesuada orci vitae nulla accumsan porta a id massa. Quisque accumsan iaculis magna sit amet fringilla. Maecenas consequat, magna eget tincidunt semper, odio nibh rutrum mi, id feugiat ante nisi eu risus. Vestibulum nunc orci, rhoncus a placerat in, ultricies in mi. Cras mattis varius eros, vel fringilla nisi suscipit eget. Quisque scelerisque sagittis nulla at porttitor.</p>
        <p>Sed id augue vitae urna euismod commodo aliquet a quam. Pellentesque arcu velit, cursus et malesuada ut, consequat et diam. Nullam erat sem, rhoncus id ullamcorper vitae, rhoncus et arcu. In ultricies ultricies nulla, ut rutrum nisi iaculis at. Donec eu magna a metus ornare faucibus. Fusce aliquet faucibus ultricies. Morbi semper, est id tincidunt gravida, sem arcu adipiscing lacus, ac bibendum nulla leo eu purus. Quisque nec diam sed risus consectetur a ccumsan quis quis nibh. Vestibulum id purus lorem.</p>
        <p>It is a long established fact that a reader will be distracted by the readable content of a page when looking at its layout. The point of using Lorem Ipsum is that it has a more-or-less normal distribution of letters, as opposed to using 'Content here, content here', making it look like readable English. Many desktop publishing packages</p>
      </div>
      <p class="closing">Sincerely,</p>
      <span class="signature" role="img" aria-label="Handwritten signature of James Hartley"></span>
    </section>

    <svg class="footer-band" viewBox="0 1020 820 130" width="820" height="130" aria-hidden="true">
      <defs>
        <linearGradient id="swoosh-fade" x1="0" x2="1" y1="0" y2="0">
          <stop offset="0" stop-color="#ffffff" stop-opacity="0"/>
          <stop offset="0.5" stop-color="#ffffff" stop-opacity="1"/>
          <stop offset="1" stop-color="#ffffff" stop-opacity="0.2"/>
        </linearGradient>
      </defs>
      <path d="M0,1058 Q420,1135 820,1026 L820,1150 L0,1150 Z" fill="var(--navy)"/>
      <path d="M160,1071 Q470,1118 780,1040 Q470,1110 160,1071 Z" fill="url(#swoosh-fade)"/>
    </svg>
    <footer class="footer-contact">Level 9, 7 Ferris Lane, Sydney NSW 2000 | 02 8472 3159 | www.qvlegal.com.au</footer>
  </main>
</body>
</html>
```